A clean crisp business card for a Landscape Construction company. Designed to be easy to read contact/ info and also be appealing/interesting, unlike a traditional business card.

Industry/Entity Type

Landscape Construction

Contact Information for Business Card

Company name : Brambleford Landscape Construction, phone number: (877) 62Vista, website:Bramblefordyards.example, Email, sales@bramblefordyards.example

Requirements
Nice to have
• Luxurious finishes/ details…. Icons or emblems next to contact info
Should not have
• Clipart or general pictures

```html
<!DOCTYPE html>
<html lang="en">
<head>
<meta charset="utf-8">
<title>Brambleford Landscape Construction – Business Card</title>
<link href="https://fonts.googleapis.com/css2?family=Source+Sans+3:wght@600;700&display=swap" rel="stylesheet">
<style>
  :root {
    --blue: #1f6ab3;
    --green: #6fbe44;
    --lime: #9dc93e;
    --white: #ffffff;
    --edge: #cfe0f3;
  }
  * { margin: 0; padding: 0; box-sizing: border-box; }
  html, body { width: 1200px; height: 942px; overflow: hidden; background: var(--white); }
  body { font-family: "Source Sans 3", "Myriad Pro", Arial, sans-serif; }
  .canvas { position: relative; width: 1200px; height: 942px; }
  .artwork { position: absolute; inset: 0; }
  .text { position: absolute; color: var(--lime); font-weight: 700; white-space: nowrap; }

  .brand { position: absolute; text-align: center; color: var(--blue); font-weight: 700; line-height: 1.05; }
  .brand-front { left: 0; width: 566px; top: 164px; }
  .brand-front .brand-name { font-size: 36px; letter-spacing: 1px; }
  .brand-front .brand-line { font-size: 12px; letter-spacing: 3.5px; text-transform: uppercase; margin-top: 4px; }
  .brand-back { left: 635px; width: 565px; top: 340px; }
  .brand-back .brand-name { font-size: 56px; letter-spacing: 1.5px; }
  .brand-back .brand-line { font-size: 17px; letter-spacing: 6px; text-transform: uppercase; margin-top: 8px; }

  .person-name { left: 0; width: 546px; text-align: center; top: 552px; font-size: 38px; letter-spacing: .5px; text-transform: uppercase; }
  .person-role { left: 187px; width: 192px; text-align: center; top: 619px; font-size: 19px; font-weight: 600; }
  .contact-phone { left: 216px; top: 694px; font-size: 19px; }
  .contact-email { left: 216px; top: 773px; font-size: 15.5px; }
  .contact-address { left: 215px; top: 833px; font-size: 15.5px; line-height: 1.35; white-space: normal; width: 300px; }
  .website { left: 815px; top: 852px; font-size: 15.5px; }
</style>
</head>
<body>
<div class="canvas">
  <svg class="artwork" viewBox="0 0 1434 1126" width="1200" height="942" aria-hidden="true">
    <defs>
      <linearGradient id="leafBand" x1="0" y1="0" x2="1" y2="0">
        <stop offset="0" stop-color="#6fbe44"/>
        <stop offset="1" stop-color="#9dc93e"/>
      </linearGradient>
    </defs>

    <!-- front card -->
    <rect x="0" y="0" width="676" height="1126" fill="var(--white)"/>
    <circle cx="342" cy="165" r="32" fill="var(--green)"/>
    <g role="img" aria-label="Decorative geometric band in green tones">
      <polygon points="0,325 676,383 676,600 0,720" fill="url(#leafBand)"/>
    </g>
    <polygon points="0,700 676,480 676,1126 0,1126" fill="var(--blue)"/>
    <line x1="223" y1="773" x2="453" y2="773" stroke="var(--lime)" stroke-width="3"/>

    <circle cx="202" cy="845" r="34" fill="var(--lime)"/>
    <rect x="190" y="826" width="24" height="38" rx="4" fill="none" stroke="var(--white)" stroke-width="3"/>
    <line x1="193" y1="855" x2="211" y2="855" stroke="var(--white)" stroke-width="2"/>
    <circle cx="202" cy="859.5" r="1.6" fill="var(--white)"/>

    <circle cx="202" cy="930" r="34" fill="var(--lime)"/>
    <g fill="none" stroke="var(--white)" stroke-width="3" stroke-linejoin="round">
      <rect x="182" y="928" width="22" height="12" rx="3" transform="rotate(-40 193 934)"/>
      <rect x="200" y="918" width="22" height="12" rx="3" transform="rotate(-40 211 924)"/>
    </g>

    <circle cx="202" cy="1015" r="34" fill="var(--lime)"/>
    <path d="M202 1036 C193 1024 189 1017 189 1009 A13 13 0 0 1 215 1009 C215 1017 211 1024 202 1036 Z" fill="var(--white)"/>
    <circle cx="202" cy="1009" r="5" fill="var(--lime)"/>

    <!-- back card -->
    <rect x="759.5" y="0.5" width="674" height="1125" fill="var(--white)" stroke="var(--edge)" stroke-width="1"/>
    <circle cx="1083" cy="330" r="44" fill="var(--green)"/>
    <g role="img" aria-label="Decorative geometric band in green tones">
      <polygon points="759,750 1434,575 1434,1000 759,1000" fill="url(#leafBand)"/>
    </g>
    <polygon points="759,960 1434,860 1434,1126 759,1126" fill="var(--blue)"/>

    <g fill="none" stroke="var(--lime)" stroke-width="2.5">
      <circle cx="952" cy="1032" r="11"/>
      <path d="M941 1032 H963 M952 1021 C946 1027 946 1037 952 1043 M952 1021 C958 1027 958 1037 952 1043"/>
    </g>
  </svg>

  <div class="brand brand-front">
    <div class="brand-name">Brambleford</div>
    <div class="brand-line">Landscape Construction</div>
  </div>

  <div class="text person-name">Dara Venn</div>
  <div class="text person-role">Sales Manager</div>
  <div class="text contact-phone">(555) 218 3307</div>
  <div class="text contact-email">sales@bramblefordyards.example</div>
  <div class="text contact-address">4170 Harrow Creek Rd., Suite 118, Millbrook, OH 45990</div>

  <div class="brand brand-back">
    <div class="brand-name">Brambleford</div>
    <div class="brand-line">Landscape Construction</div>
  </div>
  <div class="text website">bramblefordyards.example</div>
</div>
</body>
</html>
```